I need a header for the web site www.halvertonpipeworks.com/demo
It must include the following
Existig Logo (I will upload the .png)
Text: Serving Calgary and Surrounding Areas for Over 30 Years!
24 Hour Service
Call 587.214.7093 (Note this isn't the actual phone number I will need to be able to change the Phone number once the site is ready to put in a tracking number so I am hoping I get a PSD file with this where the text is editable)
We wnat the feel to be warm and geared more towards a residential customer rather than an industial customer.
We would like blue tones but are open to anything warm.

Size: Aprroximately 960x300

Residential

Requirements
Must have
• Rounded Corners to match the content area on the site

```html
<!DOCTYPE html>
<html lang="en">
<head>
<meta charset="utf-8">
<title>Halverton Pipeworks – Header</title>
<link rel="stylesheet" href="https://fonts.googleapis.com/css2?family=Arimo:wght@400;700&family=Tinos:wght@400&display=swap">
<style>
  :root {
    --frame: #3b4046;
    --sky-top: #aebfd2;
    --sky-mid: #7f9cbd;
    --sky-deep: #2f4d74;
    --band: rgba(255, 255, 255, 0.5);
    --band-edge: rgba(255, 255, 255, 0.85);
    --ink: #2b2e33;
    --service: #dfe4ea;
  }
  html, body {
    margin: 0;
    width: 1200px;
    height: 375px;
    overflow: hidden;
    background: #ffffff;
  }
  .site-header {
    position: relative;
    width: 1200px;
    height: 375px;
    box-sizing: border-box;
    border: 6px solid var(--frame);
    border-radius: 16px;
    overflow: hidden;
  }
  .sky-photo {
    position: absolute;
    inset: 0;
    background:
      radial-gradient(ellipse 420px 160px at 760px 150px, rgba(255,255,255,0.55), transparent 70%),
      radial-gradient(ellipse 360px 120px at 220px 60px, rgba(255,255,255,0.35), transparent 70%),
      linear-gradient(180deg, var(--sky-top) 0%, var(--sky-mid) 45%, var(--sky-deep) 100%);
  }
  .header-art {
    position: absolute;
    inset: 0;
    width: 100%;
    height: 100%;
  }
  .tagline {
    font-family: "Arimo", Arial, sans-serif;
    font-size: 34px;
    fill: var(--ink);
  }
  .brand-name {
    position: absolute;
    top: 14px;
    left: 0;
    right: 0;
    margin: 0;
    text-align: center;
    font-family: "Tinos", "Times New Roman", serif;
    font-weight: 400;
    font-size: 37px;
    letter-spacing: 3px;
    color: var(--ink);
    text-transform: uppercase;
  }
  .service-line {
    position: absolute;
    bottom: 6px;
    margin: 0;
    font-family: "Arimo", Arial, sans-serif;
    font-weight: 700;
    font-size: 48px;
    color: var(--service);
    line-height: 1;
  }
  .service-hours { left: 18px; }
  .service-phone { right: 14px; }
</style>
</head>
<body>
  <header class="site-header">
    <div class="sky-photo" role="img" aria-label="Photograph of a blue sky with sunlit white clouds"></div>

    <svg class="header-art" viewBox="0 0 1188 363" aria-hidden="true">
      <path class="top-band" d="M0,0 H1188 V166 Q555,324 0,144 Z" fill="var(--band)" />
      <path class="top-band-edge" d="M1188,166 Q555,324 0,144" fill="none" stroke="var(--band-edge)" stroke-width="2" />
      <defs>
        <path id="tagline-curve" d="M44,128 Q595,300 1140,160" />
      </defs>
      <text class="tagline">
        <textPath href="#tagline-curve" textLength="1090" lengthAdjust="spacing">Serving Calgary and surrounding areas for over 30 Years!</textPath>
      </text>
    </svg>

    <h1 class="brand-name">Halverton Pipeworks</h1>

    <p class="service-line service-hours">24 HOUR SERVICE</p>
    <p class="service-line service-phone">Call 587.214.7093</p>
  </header>
</body>
</html>
```